Building company buisness cards

We are looking for a sharp modern new look for our business cards.
We are a New Zealand based company that specialises in house and land packages.
We have attached a photo of the current logo and would like to see if it can be improved somehow if needed.
We are open to any colours but we have chosen green at this stage.
Feel free to change the font and make the logo smarter looking.
Play with the colours and see what looks best.

We want a card that looks so good know one will want to throw it away!

Target Market(s)

Home buyers

Industry/Entity Type

Building

Contact Information for Business Card

Derek Tolvane
0217394062
dtolvane@quillmarkhomesteads.co.nz
quillmarkhomesteads.co.nz

Font styles to use
Serif
Sans Serif

Colors

Designer to choose colors to be used in the design.

Requirements
Must have
• Logo and company name on one side, details on the other side
Nice to have
• Color codes for the original green are HEX #4a8028, RGB(74,128,40), CMYK(42,0,69,50)
• Round corners, Raised and/or spot UV

```html
<!DOCTYPE html>
<html lang="en">
<head>
<meta charset="utf-8">
<title>Quillmark Homesteads — Business Cards</title>
<link rel="stylesheet" href="https://fonts.googleapis.com/css2?family=Montserrat:wght@400;600&display=swap">
<style>
  :root {
    --backdrop: #161616;
    --card: #262626;
    --card-edge: #2e2e2e;
    --green: #4a8028;
    --green-bright: #4f9a2c;
    --silver: #8a8a8a;
    --ink: #f2f2f2;
  }
  * { box-sizing: border-box; margin: 0; padding: 0; }
  html, body {
    width: 1200px; height: 900px; overflow: hidden;
    background: var(--backdrop);
    font-family: "Montserrat", sans-serif;
  }
  .sheet {
    width: 1200px; height: 900px;
    display: flex; flex-direction: column; align-items: center; justify-content: center;
    gap: 40px;
  }
  .card {
    position: relative;
    width: 700px; height: 400px;
    background: linear-gradient(135deg, var(--card-edge), var(--card));
    border-radius: 6px;
    overflow: hidden;
  }
  .card::after {
    content: ""; position: absolute; left: 0; right: 0; bottom: 0;
    height: 5px; background: var(--green-bright);
  }
  .brand {
    display: flex; align-items: center;
    font-weight: 600; white-space: nowrap;
  }
  .brand-mark { flex: none; background: currentColor; }
  .card-front {
    display: flex; align-items: center; justify-content: center;
  }
  .brand-large { color: var(--silver); font-size: 42px; gap: 18px; }
  .brand-large .brand-mark { width: 40px; height: 40px; }
  .card-back {
    display: flex; align-items: center;
    padding: 0 30px 20px 40px;
  }
  .brand-small { color: var(--green-bright); font-size: 18px; gap: 10px; }
  .brand-small .brand-mark { width: 18px; height: 18px; }
  .divider {
    width: 2px; height: 130px; background: var(--green-bright);
    margin: 0 26px; flex: none;
  }
  .details { color: var(--ink); }
  .person-name {
    font-weight: 600; color: var(--green-bright);
    font-size: 25px; letter-spacing: 0.5px;
  }
  .person-role { font-size: 19px; margin-bottom: 14px; }
  .contact-list { list-style: none; font-size: 16px; line-height: 1.55; }
  .contact-list li { display: flex; align-items: center; gap: 9px; white-space: nowrap; }
  .contact-list svg { width: 13px; height: 13px; flex: none; }
</style>
</head>
<body>
<main class="sheet">
  <section class="card card-front" aria-label="Card front">
    <p class="brand brand-large"><span class="brand-mark" aria-hidden="true"></span>Quillmark Homesteads</p>
  </section>

  <section class="card card-back" aria-label="Card back">
    <p class="brand brand-small"><span class="brand-mark" aria-hidden="true"></span>Quillmark Homesteads</p>
    <div class="divider"></div>
    <div class="details">
      <p class="person-name">Derek Tolvane</p>
      <p class="person-role">Founder</p>
      <ul class="contact-list">
        <li>
          <svg viewBox="0 0 16 16" aria-hidden="true"><path d="M4 1l3 3-2 2c1 2 3 4 5 5l2-2 3 3-2 2C7 14 2 9 2 3z" fill="none" stroke="#4f9a2c" stroke-width="1.4"/></svg>
          0217394062
        </li>
        <li>
          <svg viewBox="0 0 16 16" aria-hidden="true"><rect x="1.5" y="3.5" width="13" height="9" fill="none" stroke="#4f9a2c" stroke-width="1.4"/><path d="M1.5 3.5l6.5 5 6.5-5" fill="none" stroke="#4f9a2c" stroke-width="1.4"/></svg>
          dtolvane@quillmarkhomesteads.co.nz
        </li>
        <li>
          <svg viewBox="0 0 16 16" aria-hidden="true"><circle cx="8" cy="8" r="6.5" fill="none" stroke="#4f9a2c" stroke-width="1.4"/><ellipse cx="8" cy="8" rx="3" ry="6.5" fill="none" stroke="#4f9a2c" stroke-width="1.2"/><path d="M1.5 8h13" stroke="#4f9a2c" stroke-width="1.2"/></svg>
          quillmarkhomesteads.co.nz
        </li>
      </ul>
    </div>
  </section>
</main>
</body>
</html>
```